Tandem Hearth Works Pty Ltd

We need business cards for a company based in Perth, we install, service and maintain fire equipment.
On the front we want a great design with our logo and a small spot for our full company name, general company email address and office number. On the back we need space for our name, title, mobile number and email address on the back.

Target Market(s)

Facility managers and commercial/industrial building owners/occupiers.

Contact Information for Business Card

Font styles to use
Sans Serif

Requirements
Must have
• Please only submit 5 of your best samples.
Darker tones are preferred.
Nice to have
• We want to use, black, red and grey. Keep it modern and clean.
I've attached the company logo and a sample of a boarder we use on our emergency plans.
Should not have
• No preference. Let the designer choose.

```html
<!DOCTYPE html>
<html lang="en">
<head>
<meta charset="utf-8">
<title>Tandem Hearth Works – Business Cards</title>
<link href="https://fonts.googleapis.com/css2?family=Arimo:wght@400;700&display=swap" rel="stylesheet">
<style>
  :root {
    --brand-red: #ec1c24;
    --brand-grey: #9a9a9f;
    --ink: #2b2b2b;
    --paper: #ffffff;
    --backdrop: #e9e7e4;
  }
  * { box-sizing: border-box; margin: 0; padding: 0; }
  html, body { width: 1200px; height: 900px; overflow: hidden; }
  body {
    background: var(--backdrop);
    font-family: "Arimo", Arial, sans-serif;
    display: flex;
    align-items: center;
    justify-content: center;
    gap: 40px;
  }
  .card {
    position: relative;
    width: 560px;
    height: 320px;
    overflow: hidden;
    box-shadow: 0 10px 28px rgba(0,0,0,.22);
  }
  .card--front { background: var(--brand-red); color: var(--paper); }
  .card--back { background: var(--paper); color: var(--ink); }

  .company {
    position: absolute; left: 44px; top: 44px;
    font-weight: 700; text-transform: uppercase;
    font-size: 17px; line-height: 1.1; letter-spacing: .3px;
  }
  .company__phone { display: block; font-size: 23px; margin-top: 6px; letter-spacing: .5px; }

  .wordmark {
    position: absolute; right: 44px; top: 44px;
    font-weight: 700; font-size: 72px; line-height: 1; letter-spacing: 2px;
  }
  .card--front .wordmark { color: var(--paper); }
  .card--back .wordmark { color: var(--brand-red); }

  .contact-list {
    position: absolute; list-style: none;
    font-size: 17px; line-height: 1.45;
  }
  .card--front .contact-list { left: 44px; bottom: 36px; }
  .card--back .contact-list { left: 70px; top: 164px; font-size: 18px; color: var(--ink); }
  .contact-list li { display: flex; align-items: center; gap: 12px; }
  .contact-list svg { width: 20px; height: 20px; flex: none; }

  .person { position: absolute; left: 44px; top: 92px; }
  .person__name {
    color: var(--brand-red); font-weight: 700; text-transform: uppercase;
    font-size: 25px; letter-spacing: .3px;
  }
  .person__title { font-size: 18px; margin-top: 2px; }

  .swoosh { position: absolute; inset: 0; width: 100%; height: 100%; }
</style>
</head>
<body>

  <section class="card card--front" aria-label="Business card front">
    <p class="company">Tandem Hearth<br>Works Pty Ltd
      <span class="company__phone">555.0140.2260</span>
    </p>
    <div class="wordmark">THW</div>
    <ul class="contact-list">
      <li>
        <svg viewBox="0 0 20 20" aria-hidden="true"><rect x="1.5" y="4.5" width="17" height="11" fill="none" stroke="#fff" stroke-width="1.6"/><path d="M1.5 4.5 10 11l8.5-6.5" fill="none" stroke="#fff" stroke-width="1.6"/></svg>
        info@tandemhearth.com
      </li>
      <li>
        <svg viewBox="0 0 20 20" aria-hidden="true"><g fill="none" stroke="#fff" stroke-width="1.4"><circle cx="10" cy="10" r="8"/><ellipse cx="10" cy="10" rx="3.5" ry="8"/><path d="M2 10h16M3.2 6h13.6M3.2 14h13.6"/></g></svg>
        www.tandemhearth.com
      </li>
    </ul>
  </section>

  <section class="card card--back" aria-label="Business card back">
    <svg class="swoosh" viewBox="0 0 560 320" preserveAspectRatio="none" aria-hidden="true">
      <path d="M0 262 C190 264 320 242 415 188 C330 246 190 278 0 278 Z" fill="var(--brand-grey)"/>
      <path d="M0 281 C190 281 330 252 432 182 C482 148 526 130 560 124 L560 320 L0 320 Z" fill="var(--brand-red)"/>
    </svg>
    <div class="person">
      <h1 class="person__name">Marcus Ellery</h1>
      <p class="person__title">Managing Director</p>
    </div>
    <div class="wordmark">THW</div>
    <ul class="contact-list">
      <li>
        <svg viewBox="0 0 20 20" aria-hidden="true"><rect x="5" y="1.5" width="10" height="17" rx="2" fill="none" stroke="var(--brand-red)" stroke-width="1.8"/><circle cx="10" cy="15.5" r="1" fill="var(--brand-red)"/></svg>
        555.0187.3321
      </li>
      <li>
        <svg viewBox="0 0 20 20" aria-hidden="true"><rect x="1.5" y="4.5" width="17" height="11" fill="var(--brand-red)"/><path d="M1.5 4.5 10 11l8.5-6.5" fill="none" stroke="#fff" stroke-width="1.4"/></svg>
        name@tandemhearth.com
      </li>
    </ul>
  </section>

</body>
</html>
```